WordPress Website for BidLinks Agency

We are in need of a complete WordPress design.

We will be seeking new clients and we want them to have a great idea of what our business does when they get to the page along with the products and services we offer. Our current website is www.mossyharbor.com and it really needs an upgrade. Wordpress would be great but our owner knows HTML as well so he can go in and edit things later if need be. Please apply if you can show what a Search Engine Marketing company does and can explain this information to a lay person. Also, the website should be responsive so it fits mobile, tablet, and desktop settings while changing to these different widths.

Also, we are not an SEO company, per se but an SEM / PPC company that operates on Zorvic BidLinks, Plim Promos, Chatterwall Promos, and other PPC platforms.

Themes are fine just as long as the content and the visuals display what a search engine marketing company does. Really looking for clients to know exactly why a search engine marketing company does when the get to the site, why they should use a search engine marketing company, and the best way to contact us to get a quote.

Here are some other search engine marketing sites that I like in terms of the content and the layout to give an idea of what should be included on the site:
http://www.fendowlabs.com/
http://www.k9rworks.com/
http://www.boulderpartners.com/
http://www.vjnpromo.com/
http://www.halvorteam.com/
http://meetthepinecrew.com/

Please include my new phone number of the website: 866-555-0142.

Thank you, 
Walt 

Target Market(s)

We are a search engine marketing company looking for more clients and want to be able to explain what a search engine marketing company does in layman's terms.

Industry/Entity Type

Marketing

Font styles to use
Sans Serif

Requirements
Must have
• About Us Page
Services Page
Home Page
Success Stories Page
Blog
Social Media links / feeds
Visuals of products / services offered
Jobs page
Nice to have
• Responsive design
Client Login / Space on the site for monthly client payments / Link to CoinTap or Rivermoss

```html
<!DOCTYPE html>
<html lang="en">
<head>
<meta charset="utf-8">
<title>Mossy Harbor – SEM Business Program</title>
<link rel="stylesheet" href="https://fonts.googleapis.com/css2?family=Open+Sans:wght@300;400;600;700&family=Roboto+Condensed:wght@400;700&family=Rokkitt:wght@400;500&family=Arimo:wght@400;700&display=swap">
<style>
:root{
  --red:#e2231f;
  --ink:#333;
  --grey:#6d6d6d;
  --soft:#9a9a9a;
  --line:#e4e4e4;
  --teal:#1aa3c9;
  --blue:#1f7ec4;
  --dark:#3c3c3c;
  --service:#7a7a7a;
  --hero:#e8f0f8;
  --yellow:#f3d21b;
}
*{box-sizing:border-box;margin:0;padding:0}
html,body{width:969px;height:1200px;overflow:hidden;background:#fff}
body{font-family:"Arimo",Arial,sans-serif;color:var(--ink);position:relative}
.abs{position:absolute}
.topline{left:0;top:0;width:969px;height:3px;background:#4a4a4a}
.hero-bg{left:0;top:119px;width:969px;height:1081px;background:linear-gradient(180deg,var(--hero) 0,#f2f6fb 300px,#f5f7fa 100%)}
.brand{left:68px;top:38px;font-family:"Arimo",sans-serif;font-weight:700;font-size:22px;color:var(--ink)}
.callbox{left:659px;top:25px;width:233px;height:42px;background:#555;clip-path:polygon(0 0,100% 0,100% 100%,0 100%,10px 50%);border-radius:0 4px 4px 0;color:#fff}
.callbox .call{position:absolute;left:20px;top:5px;font-family:"Rokkitt",serif;font-size:15px;letter-spacing:.5px}
.callbox .call b{font-family:"Arimo",sans-serif;font-weight:400;font-size:19px;margin-left:4px}
.callbox .back{position:absolute;right:10px;top:26px;font-size:9.5px}
.callbox .back a{color:var(--yellow)}
.utility{left:683px;top:81px;font-size:9.5px;color:#444;display:flex;align-items:center;gap:6px}
.utility .sep{color:#bbb}
.social{display:flex;gap:6px;margin-left:12px}
.social span{width:13px;height:13px;border-radius:2px;background:#3b5998}
.social span:nth-child(2){background:#3fb4e6}
.social span:nth-child(3){background:#48a23e}
.social span:nth-child(4){background:#6a7fa3}
.nav{left:67px;top:101px;width:832px;height:18px;border-bottom:1px solid #dfe3ea;font-size:14px;color:var(--red)}
.nav span{position:absolute;top:0}
.nav i{position:absolute;top:3px;width:1px;height:9px;background:#c88}
.hero-photo{left:98px;top:136px;width:277px;height:282px;background:linear-gradient(160deg,#d9b49c 0,#c99a7c 40%,#7fa8d8 70%,#5f8fcf 100%);border-radius:120px 120px 0 0}
.hero-text{right:95px;top:188px;text-align:right;font-family:"Rokkitt",serif}
.hero-text .kicker{font-size:26px;color:#444;letter-spacing:-.2px}
.hero-text h1{font-weight:400;font-size:43px;color:var(--red);line-height:1;letter-spacing:.8px;margin-top:2px}
.hero-text p{font-size:15px;color:#333;line-height:19px;margin-top:8px}
.hero-cta{right:94px;top:324px;font-family:"Rokkitt",serif;font-size:17px;color:#111;display:flex;align-items:center;gap:6px}
.hero-cta svg{width:12px;height:12px}
.features{left:64px;top:418px;width:836px;height:180px;background:#fff;border-radius:4px;box-shadow:0 1px 3px rgba(0,0,0,.12)}
.tab{left:-5px;top:30px;width:21px;height:16px;background:#333;clip-path:polygon(0 0,80% 0,100% 50%,80% 100%,0 100%)}
.feature{position:absolute;top:29px;width:250px}
.feature h3{font-family:"Roboto Condensed",sans-serif;font-weight:700;font-size:15.5px;color:var(--red);letter-spacing:-.2px}
.feature p{font-size:12px;line-height:15px;color:var(--grey);letter-spacing:.6px;margin-top:5px}
.feature .more{position:absolute;top:80px;font-size:8.5px;color:#555}
.divider{position:absolute;top:22px;width:1px;height:110px;background:var(--line)}
.actionbar{left:3px;top:141px;width:830px;height:36px;background:linear-gradient(#4b4b4b,#353535);border-radius:0 0 3px 3px;font-family:"Roboto Condensed",sans-serif;font-weight:700;font-size:13.5px;color:#eee}
.actionbar span{position:absolute;top:10px;display:flex;align-items:center;gap:8px}
.actionbar em{width:12px;height:12px;display:inline-block;border-radius:1px}
.clients{left:64px;top:609px;width:836px;height:600px;background:#fff;border-radius:4px;box-shadow:0 1px 3px rgba(0,0,0,.1)}
.clients-title{left:20px;top:14px;font-family:"Open Sans",sans-serif;font-weight:300;font-size:23px;color:#444}
.clients-title b{font-weight:600}
.clients-title small{font-size:9px;color:#555;margin-left:6px;border-left:1px solid #aaa;padding-left:6px}
.client{position:absolute;top:64px;width:172px}
.shot{height:108px;border:1px solid #ddd;box-shadow:0 2px 3px rgba(0,0,0,.15)}
.client h4{font-size:12.5px;font-weight:700;color:var(--teal);margin-top:7px;letter-spacing:.3px}
.client p{font-size:10px;color:#333;margin-top:2px}
.rule{left:120px;top:231px;width:600px;height:1px;background:linear-gradient(90deg,transparent,#e6e6e6,transparent)}
.ppc{left:20px;top:278px;font-family:"Open Sans",sans-serif;color:#222}
.ppc .q{font-size:12.5px;font-weight:600;color:#555}
.ppc h2{font-size:22px;font-weight:700;line-height:26px;margin-left:3px}
.ppc .lead{font-size:14.5px;font-weight:600;line-height:19px;margin-top:10px}
.ppc .lead .blue{color:var(--blue);font-size:19.5px;line-height:24px}
.ppc .small{font-family:"Arimo",sans-serif;font-size:10px;font-weight:700;line-height:12px;margin-top:15px;margin-left:4px}
.ppc .small a{color:#5b9a1d}
.services-title{left:241px;top:250px;font-family:"Open Sans",sans-serif;font-weight:300;font-size:39px;color:#8a8a8a;letter-spacing:-.5px}
.services{left:241px;top:284px;width:189px;background:var(--service);list-style:none;padding:1px 0}
.services li{height:22.5px;border-bottom:1px solid #939393;color:#fff;font-size:12px;line-height:22px;padding-left:19px;position:relative}
.services li::before{content:"";position:absolute;left:9px;top:8px;border:3px solid transparent;border-left:4px solid #fff;border-right:0}
.services li.on{background:#8c8c8c}
.link{font-size:10px;color:#333}
.link::before{content:"";display:inline-block;margin-right:6px;border:3px solid transparent;border-left:4px solid var(--red);border-right:0}
.offers{left:456px;top:256px;width:380px}
.offers h2{font-family:"Open Sans",sans-serif;font-weight:400;font-size:15px;color:#333}
.offers ul{list-style:none;margin-top:12px}
.offers li{font-size:10px;line-height:20px;color:#333;padding-left:12px;position:relative}
.offers li::before{content:"";position:absolute;left:0;top:5px;border:4.5px solid transparent;border-left:6px solid var(--red);border-right:0}
</style>
</head>
<body>
<div class="abs topline"></div>
<div class="abs hero-bg"></div>

<header>
  <div class="abs brand">Mossy Harbor</div>
  <div class="abs callbox">
    <div class="call">CALL:<b>866-555-0142</b></div>
    <div class="back">Or leave a <a>call back request</a></div>
  </div>
  <div class="abs utility">CONTACT US <span class="sep">|</span> FOLLOW US
    <div class="social"><span></span><span></span><span></span><span></span></div>
  </div>
  <nav class="abs nav">
    <span style="left:0">Home</span><i style="left:53px"></i>
    <span style="left:70px">About Us</span><i style="left:143px"></i>
    <span style="left:152px">Product</span><i style="left:218px"></i>
    <span style="left:233px">Success Stories</span><i style="left:351px"></i>
    <span style="left:368px">Portfolio</span><i style="left:441px"></i>
    <span style="left:458px">Blog</span><i style="left:512px"></i>
    <span style="left:537px">Contact Us</span>
  </nav>
</header>

<section class="hero">
  <div class="abs hero-photo" role="img" aria-label="Photo of a smiling account manager in a blue cardigan"></div>
  <div class="abs hero-text">
    <div class="kicker">WE CREATE A HIGHLY RESULT-DRIVEN</div>
    <h1>SEM BUSINESS PROGRAM</h1>
    <p>We help you to beat your competitors in search engine rankings by being<br>on Zorvic's first page for all your business keywords.</p>
  </div>
  <div class="abs hero-cta">find out how we do this!
    <svg viewBox="0 0 12 12"><circle cx="6" cy="6" r="6" fill="#e2231f"/><path d="M5 3.5 7.5 6 5 8.5" stroke="#fff" stroke-width="1.6" fill="none"/></svg>
  </div>
</section>

<section class="abs features">
  <div class="abs tab"></div>
  <div class="feature" style="left:23px">
    <h3>DEDICATED ACCOUNT MANAGEMENT</h3>
    <p>An experienced outsourcing specialist dedicated to you to meet all of your out-sourcing needs.</p>
    <span class="more">know more »</span>
  </div>
  <div class="divider" style="left:283px"></div>
  <div class="feature" style="left:303px">
    <h3>METHODOLOGY</h3>
    <p>Daily reporting, Quality Assurance &amp; performance indicators that keep you in the loop.</p>
    <span class="more">know more »</span>
  </div>
  <div class="divider" style="left:561px"></div>
  <div class="feature" style="left:584px">
    <h3>REPUTATION</h3>
    <p>Delivering over 500 success stories in dozens of verticals in the US, UK, Australia, Ireland, &amp; Japan.</p>
    <span class="more">know more »</span>
  </div>
  <div class="abs actionbar">
    <span style="left:28px"><em style="background:#c9a064"></em>SEE OUR DETAILED SEO PACKAGES</span>
    <span style="left:317px"><em style="background:#d8382c"></em>DOWNLOAD THE PDF FILE</span>
    <span style="left:591px"><em style="background:#f1e6a8"></em>CONTACT US FOR CUSTOM QUOTES</span>
  </div>
</section>

<section class="abs clients">
  <div class="abs clients-title">Some of <b>Our Clients</b><small>view all</small></div>
  <div class="client" style="left:21px">
    <div class="shot" role="img" aria-label="Screenshot of the Fjordvika website" style="background:linear-gradient(#f6e08a 0,#f6c733 32%,#fff 32%)"></div>
    <h4>Fjordvika</h4><p><b>SERP:</b> #5 in Zorvic , #3 in Yelvo,</p>
  </div>
  <div class="client" style="left:229px">
    <div class="shot" role="img" aria-label="Screenshot of the Tutorbridge website" style="background:linear-gradient(#cfe0f2 0,#cfe0f2 10%,#fff 10%,#e5f1f9 80%,#555 80%)"></div>
    <h4>Tutorbridge</h4><p><b>SERP:</b> #5 in Zorvic , #3 in Yelvo,</p>
  </div>
  <div class="client" style="left:436px">
    <div class="shot" role="img" aria-label="Screenshot of the ShiftNestor website" style="background:linear-gradient(#fff 0,#fff 32%,#c99a3a 32%,#2d66b7 100%)"></div>
    <h4>ShiftNestor</h4><p><b>SERP:</b> #5 in Zorvic , #3 in Yelvo,</p>
  </div>
  <div class="client" style="left:644px">
    <div class="shot" role="img" aria-label="Screenshot of the Vitalmint-d website" style="background:linear-gradient(90deg,#1c74bf 0,#1c74bf 40%,#9fd15b 40%,#3aa04a 100%)"></div>
    <h4>Vitalmint-d</h4><p><b>SERP:</b> #5 in Zorvic , #3 in Yelvo,</p>
  </div>
  <div class="abs rule"></div>

  <div class="abs ppc">
    <div class="q">Why Dose your Website Need</div>
    <h2>PPC Services?</h2>
    <div class="lead">&nbsp;pay-per-click (PPC)<br>advertising &nbsp;the easy and<br><span class="blue">cost-effective way<br>of driving qualified<br>prospects</span><br>to your<br>Web site immediately</div>
    <div class="small">Why continue to give business to<br>your competition for one more day?</div>
    <div class="small" style="margin-top:10px"><a>Contact us</a> today &amp; find out how<br>quickly and easily it is to begin<br>increasing your web, web traffic and<br>online business sales.</div>
  </div>

  <div class="abs services-title">Services</div>
  <ul class="abs services">
    <li>SEO</li><li>Article Submission</li><li>Directory Submission</li><li class="on">Blog Creation</li>
    <li>Blog Commenting</li><li>Link Building</li><li>Social Bookmarking</li><li>Contextual Blogpost</li>
    <li>Video Marketing</li><li>Local Search Marketing</li><li>Content Development</li><li>Pay Per Click</li>
  </ul>
  <div class="abs link" style="left:351px;top:576px">view all services</div>

  <div class="abs offers">
    <h2>WHAT SERVICES WE OFFERS?</h2>
    <ul>
      <li>We have over two years of Search Engine Marketing experience, especially in Zorvic BidLinks.</li>
      <li>We can handle all types of budgets, large and small.</li>
      <li>We are able to work on client websites to optimize conversion paths using data from Zorvic Metrics.</li>
      <li>This cuts down on clicks without conversions.</li>
      <li>We are in business for the long-term and seek long-term partnerships with businesses to help them grow.</li>
      <li>We help businesses get found online.</li>
      <li>We solve the problem of low traffic and low sales from their sites.</li>
      <li>We educate our clients in terms of best practices for their websites.</li>
      <li>We offer a dedicated account representative along with weekly and monthly reporting.</li>
      <li>We care about our clients and we really like seeing businesses grow.</li>
    </ul>
  </div>
  <div class="abs link" style="left:749px;top:576px">know more</div>
</section>
</body>
</html>
```